Window cleaning and Pressure washing

Truck wrap partial or full/background:
Would like to see a background of a water mark or something related to window cleaning. And or pressure washing.

Doors of the truck:
Need to have my logo printed in big on the doors and with LLC in small after the logo. Need to have my slogan below my logo on the door.
Slogan is; “Affordable 5 star services!”

Sides of the truck:
Want to see window cleaning and Pressure washing on the sides of the truck in big letters with the phone number. Slanted with a shadow effect.
(Would like to see slanted and not slanted) also need to see something that signifies 100% satisfaction or your money back!Preferably a sticker, Or a combination of both. Also need to have residential and commercial somewhere.
Phone number needs to be on here.

Tailgate:
Want to have the services on the back tailgate with the slogan, as well as the 100% money back guarantee sticker.
And the phone number here to!

Back window;
Needs to have the same background as the wrap on the truck or very slimier with the water swiped away Clean with the logo presented as shown in one of the pictures below.

```html
<!DOCTYPE html>
<html lang="en">
<head>
<meta charset="utf-8">
<title>The Clear Path LLC – Truck Wrap</title>
<link href="https://fonts.googleapis.com/css2?family=Montserrat:wght@600;700;800;900&family=Oswald:wght@500;700&display=swap" rel="stylesheet">
<style>
  :root{
    --stage:#676767;
    --sky:#2fb3f0;
    --sky-light:#8fdcfb;
    --sky-deep:#1593d6;
    --ink:#1b1b1b;
    --slate:#3c3d3f;
    --white:#ffffff;
    --gold:#f7a21b;
    --star:#f6c90e;
  }
  html,body{margin:0;padding:0;overflow:hidden;background:var(--stage);}
  .wrap-sheet{display:block;width:1094px;height:1200px;}
  .font-logo{font-family:"Montserrat",sans-serif;font-weight:900;}
  .font-label{font-family:"Montserrat",sans-serif;font-weight:700;}
  .font-service{font-family:"Oswald",sans-serif;font-weight:500;}
  .font-phone{font-family:"Oswald",sans-serif;font-weight:700;}
  .service-side{fill:var(--slate);stroke:var(--white);stroke-width:2.5;paint-order:stroke;}
  .service-gate{fill:var(--white);stroke:#2a6f98;stroke-width:1.2;paint-order:stroke;}
  .phone-text{fill:#e9e9e9;}
</style>
</head>
<body>
<svg class="wrap-sheet" viewBox="0 0 1241 1362" xmlns="http://www.w3.org/2000/svg">
  <defs>
    <linearGradient id="water" x1="0" y1="0" x2="1" y2="1">
      <stop offset="0" stop-color="#4cc3f5"/>
      <stop offset="0.5" stop-color="var(--sky)"/>
      <stop offset="1" stop-color="#57cdf8"/>
    </linearGradient>
    <linearGradient id="scene" x1="0" y1="0" x2="1" y2="1">
      <stop offset="0" stop-color="#c9d6dc"/>
      <stop offset="0.45" stop-color="#8c9a9e"/>
      <stop offset="0.8" stop-color="#d9dccf"/>
      <stop offset="1" stop-color="#9bb36a"/>
    </linearGradient>
    <linearGradient id="gold" x1="0" y1="0" x2="0" y2="1">
      <stop offset="0" stop-color="#ffd347"/>
      <stop offset="1" stop-color="#f08a12"/>
    </linearGradient>
    <clipPath id="truck-body">
      <path d="M112,240 L128,228 L340,214 Q392,188 424,166 L520,110 Q560,100 650,100 L660,103 Q668,140 668,205 L1125,205 L1130,236 L1120,246 L1126,320 L1100,332 L1100,396 L862,396 Q852,328 792,325 Q732,330 726,396 L345,396 Q332,300 265,300 Q202,304 186,330 L162,312 L112,300 Z"/>
    </clipPath>
    <clipPath id="rear-glass">
      <path d="M205,1192 L255,950 Q262,935 290,932 Q640,905 1010,930 Q1028,932 1030,950 L1036,1192 Z"/>
    </clipPath>
    <symbol id="tick" viewBox="0 0 24 24">
      <circle cx="12" cy="12" r="10.5" fill="var(--white)" stroke="var(--gold)" stroke-width="2.4"/>
      <path d="M7 12.3 L10.6 15.6 L17 8.8" fill="none" stroke="var(--gold)" stroke-width="2.6" stroke-linecap="round" stroke-linejoin="round"/>
    </symbol>
    <symbol id="phone-icon" viewBox="0 0 40 40">
      <circle cx="20" cy="20" r="17" fill="none" stroke="var(--white)" stroke-width="3.5"/>
      <path d="M14 11 l4 -1 l2.5 6 l-3 2 q2 5 6 7 l2 -3 l6 2.5 l-1 4 q-2 2 -6 1 q-10 -4 -13 -13 q-1 -4 2.5 -6.5z" fill="var(--white)"/>
    </symbol>
    <symbol id="star" viewBox="0 0 20 20">
      <path d="M10 1 L12.6 7 L19 7.4 L14 11.6 L15.6 18 L10 14.4 L4.4 18 L6 11.6 L1 7.4 L7.4 7 Z" fill="var(--star)"/>
    </symbol>
  </defs>

  <!-- ===== Side panel ===== -->
  <g class="side-panel">
    <g clip-path="url(#truck-body)">
      <rect x="100" y="95" width="1040" height="310" fill="url(#water)"/>
      <polygon points="760,205 1140,205 1140,400 800,400" fill="var(--white)"/>
      <polygon points="700,205 780,205 820,400 720,400" fill="var(--white)" opacity="0.55"/>
      <polygon points="820,205 1135,205 1120,250 800,250" fill="var(--slate)"/>
      <polygon points="365,332 620,332 612,358 355,358" fill="var(--slate)"/>
      <polygon points="402,360 690,360 680,392 392,392" fill="var(--sky-deep)"/>
    </g>
    <path d="M422,202 Q472,142 560,116 L610,114 Q626,114 626,130 L628,210 L442,224 Z" fill="var(--white)"/>

    <text x="272" y="244" text-anchor="middle" class="font-label" font-size="14" fill="var(--ink)">LICENCED BONDED</text>
    <rect x="196" y="248" width="152" height="18" fill="var(--ink)"/>
    <text x="272" y="262" text-anchor="middle" class="font-label" font-size="14" fill="var(--white)">AND INSURED</text>

    <g class="brand-name font-logo" fill="var(--ink)">
      <text x="404" y="262" font-size="28">THE</text>
      <text x="404" y="294" font-size="34">CLEAR</text>
      <text x="430" y="322" font-size="26">PATH <tspan font-size="14">LLC</tspan></text>
    </g>
    <text x="488" y="352" text-anchor="middle" class="font-label" font-size="22" fill="var(--white)">AFFORDABLE</text>
    <text x="540" y="382" text-anchor="middle" class="font-label" font-size="24" fill="var(--white)">5 STAR SERVICES!</text>

    <use href="#tick" x="633" y="235" width="20" height="20"/>
    <use href="#tick" x="633" y="297" width="20" height="20"/>
    <g class="font-service service-side" font-size="29">
      <text x="660" y="258">WINDOW</text>
      <text x="660" y="288">CLEANING AND</text>
      <text x="660" y="318">MOSS</text>
      <text x="660" y="348">REMOVAL</text>
    </g>

    <circle cx="810" cy="230" r="18" fill="var(--sky)"/>
    <use href="#phone-icon" x="795" y="215" width="30" height="30"/>
    <text x="840" y="245" class="font-phone phone-text" font-size="38">(555) 014-2290</text>
    <rect x="864" y="254" width="204" height="20" fill="var(--sky)"/>
    <text x="966" y="269" text-anchor="middle" class="font-label" font-size="14" fill="var(--white)">theclearpathllc.com</text>

    <g class="guarantee-small">
      <text x="1054" y="310" text-anchor="middle" class="font-phone" font-size="26" fill="url(#gold)">100%</text>
      <rect x="1024" y="315" width="62" height="24" rx="3" fill="var(--slate)"/>
      <text x="1055" y="325" text-anchor="middle" class="font-service" font-size="8" fill="var(--white)">SATISFACTION OR</text>
      <rect x="1027" y="328" width="56" height="8" fill="var(--white)"/>
      <text x="1055" y="335" text-anchor="middle" class="font-label" font-size="6" fill="var(--sky-deep)">YOUR MONEY BACK!</text>
      <use href="#star" x="1030" y="342" width="8" height="8"/>
      <use href="#star" x="1041" y="342" width="8" height="8"/>
      <use href="#star" x="1052" y="342" width="8" height="8"/>
      <use href="#star" x="1063" y="342" width="8" height="8"/>
      <use href="#star" x="1074" y="342" width="8" height="8"/>
      <circle cx="1034" cy="370" r="6" fill="#8a8a8a"/>
      <circle cx="1053" cy="370" r="6" fill="#8a8a8a"/>
      <circle cx="1072" cy="370" r="6" fill="#8a8a8a"/>
    </g>
  </g>

  <!-- ===== Tailgate ===== -->
  <g class="tailgate">
    <path d="M205,812 L207,497 L212,497 L230,533 L1015,533 L1020,500 L1034,500 L1036,812 Z" fill="url(#water)"/>
    <rect x="548" y="547" width="150" height="65" rx="12" fill="var(--white)"/>
    <polygon points="850,715 1036,715 1036,812 885,812" fill="var(--white)"/>
    <polygon points="205,715 840,715 885,812 205,812" fill="var(--slate)"/>
    <polygon points="205,715 255,715 310,812 205,812" fill="var(--sky)"/>
    <circle cx="270" cy="763" r="34" fill="var(--sky)"/>
    <use href="#phone-icon" x="236" y="729" width="68" height="68"/>
    <text x="330" y="792" class="font-phone phone-text" font-size="76">(555) 014-2290</text>

    <text x="621" y="665" text-anchor="middle" class="font-label" font-size="16" fill="var(--white)">ROADLINE</text>

    <g class="font-service service-gate" font-size="32">
      <use href="#tick" x="243" y="562" width="26" height="26"/>
      <text x="281" y="588">WINDOW CLEANING</text>
      <use href="#tick" x="243" y="609" width="26" height="26"/>
      <text x="281" y="635">PRESSURE WASHING</text>
      <use href="#tick" x="243" y="656" width="26" height="26"/>
      <text x="281" y="682">SNOW REMOVAL</text>
      <use href="#tick" x="730" y="562" width="26" height="26"/>
      <text x="768" y="588">GUTTER CLEANING</text>
      <use href="#tick" x="730" y="609" width="26" height="26"/>
      <text x="768" y="635">MOSS REMOVAL</text>
      <use href="#tick" x="730" y="656" width="26" height="26"/>
      <text x="768" y="682">HOLIDAY LIGHTS</text>
    </g>

    <g class="guarantee-sticker">
      <text x="944" y="734" text-anchor="middle" class="font-phone" font-size="48" fill="url(#gold)">100%</text>
      <rect x="886" y="738" width="116" height="36" rx="4" fill="var(--slate)"/>
      <text x="944" y="753" text-anchor="middle" class="font-service" font-size="14" fill="var(--white)">SATISFACTION OR</text>
      <rect x="892" y="757" width="104" height="13" fill="var(--white)"/>
      <text x="944" y="767" text-anchor="middle" class="font-label" font-size="10" fill="var(--sky-deep)">YOUR MONEY BACK!</text>
      <use href="#star" x="903" y="783" width="12" height="12"/>
      <use href="#star" x="921" y="783" width="12" height="12"/>
      <use href="#star" x="939" y="783" width="12" height="12"/>
      <use href="#star" x="957" y="783" width="12" height="12"/>
      <use href="#star" x="975" y="783" width="12" height="12"/>
    </g>
  </g>

  <!-- ===== Rear window ===== -->
  <g class="rear-window" clip-path="url(#rear-glass)">
    <rect x="200" y="900" width="840" height="300" fill="url(#water)"/>
    <polygon points="800,900 1040,900 1040,1200 525,1200" fill="url(#scene)" role="img" aria-label="Photo of a gloved hand squeegeeing a soapy window with a house in the background"/>
    <line x1="800" y1="900" x2="525" y2="1200" stroke="var(--white)" stroke-width="6"/>
  </g>
  <g class="brand-name-large font-logo" fill="var(--ink)">
    <text x="292" y="1025" font-size="46">THE</text>
    <text x="310" y="1082" font-size="58">CLEAR</text>
    <text x="378" y="1128" font-size="46">PATH <tspan font-size="24">LLC</tspan></text>
  </g>
</svg>
</body>
</html>
```